Desert Basin Company Brochure

**** UPDATE 2-8-2014 ****

Size should be 11" X 17" or larger (tri or bi fold).

We're going to let the contest run it's full duration to allow for more time spent on designs.

No black backgrounds.

Consideration should be given to having the text be easy to read and in a nice, organized format.

*****************************

We're looking for an eye-catching, colorful brochure that will explain what we do, who we are... and what sets us apart from the competition.

Our company provides swimming pool service, repair, and custom renovations throughout the Phoenix, Arizona metropolitan area. These brochures will be hand-delivered to each prospective customer we visit.

The brochure will include images of our work, product logos, and a unique design that separates our company apart from the rest.

The brochure should be tri-fold. Although, if a designer wants to (or has better ideas) for a different lay-out, then we're open to seeing what can be done.

Colors we like: Blue, White, Silver, Copper, Green (accent color)

We like designs that are unique/different. Professional. Creative. Sleek. Sexy. Custom. We don't want the brochure to be "pretentious". We'd like for these brochures to leave a lasting impression with our prospective clients... and hopefully earn us more business.

We don't want the brochure to be too wordy, however if the designer feels we need to cut back (or add), let us know.

Our motto is "Every Ripple Counts".

You can view some of our projects, and what we're about either at our website (tidewellpools.example), Facebook (www.facebook/tidewellpools), or Google+ (https://plus.google.com/+Tidewellpools). Thank you!

- Print-

(Front) Logo

Service - Repair - Renovation
555-347-9180
tidewellpools.example
service@tidewellpools.example
Like Us On Facebook! Facebook LOGO
Google Plus LOGO

(Body) Why Choose Us?

Thank you for the opportunity for our company to become your pool service provider!

We’re committed to providing the best customer service possible! At the end of the day you want your pool to be clean, clear, operational, and for your service provider to be available when you need them!

We’re licensed with the Sonoran Trades Licensing Board, Bonded, and Fully Insured.
A+ reviews with the Fair Merchant Council, Corra's Picks, Brivo, Olt, Facebook, and Google!
All technicians are employees... not sub-contractors! Our employees are hard working, dependable, professional, and expected to follow our strict protocol for servicing your pool.
Flat-fee service rates! Any additional equipment repairs, maintenance, or chemical implementations are directly authorized by you!
No contracts! Our Service Level Agreement Form allows you to select your desired level of authorization for equipment repairs, filter maintenance, and extra chemical implementation programs.
Our uniformed technicians arrive in distinctive, clean GPS-tracked company trucks.
We leave detailed service slips after each service visit. In addition, all service visit information is electronically recorded and stored.
Easy, online account management to view and pay invoices or authorize estimates.
Invoices, estimates, questions, pictures, and video are communicated via e-mail!
Free service calls to diagnose equipment issues outside of our normal service.
10% Service Client Discount for all repairs and replacement items.
Tidewell Pools knows the importance of communication! We’re available by phone, email, or text all days of the week.

(Body) Our Methodology

We believe in 5 important factors in maintaining a clean, clear, and operational pool...

Good, Clean Water! Our local water supply contains high amounts of minerals. Pool chemicals add to this problem in a short amount of time. Our philosophy is to use the least amount of chemicals possible to achieve optimal water balance.
Efficient Water Flow! The invention of variable-speed pumps has enabled the ability to "dial in" proper water flow... while driving down energy costs.
Proper Filtration! Today’s high-capacity cartridge filters provide great filtration, save on wasted water from backwashing sand filters, and eliminate the need for water flow-restricting backwash valves.
Functioning Cleaning System! Having a working automatic cleaning system is vital in keeping the pool surface clean of debris and dirt... and free of staining.
A Dependable And Professional Pool Maintenance Technician! Our job is to not only oversee all of the items listed above... but to make sure your pool is in the best condition possible!

(Body) Equipment Repair & Installation

We’re educated on all phases of swimming pool equipment repair and installation... with a focus on energy-efficiency and optimum performance!

We’re an VRE & MQW Authorized Installer of variable-speed pool pumps. VRE & MQW trust us to properly install and calibrate all variable-speed pumps. We've been equipped to handle the new industry standards on variable-speed pumps since Arizona law went into effect January 1st, 2011.
We’re experts at acid washes and erasing the mineral build-up off of waterlines. All work is done in-house with our customized cleaning rig and trailer.
Heating systems. New efficiency standards have made installation and operation more affordable than ever.
Remote control automation systems. Technology now allows the user to easily view and control their entire pool system via a remote home computer, tablet, or phone!
Brilliant, color-changing LED lighting for pools and spas! The benefits of LED include brighter and broader displays... while lasting much longer than your typical light bulbs.
Salt systems provide a soft-water experience! In addition to the benefit of better feeling water, salt systems generate plenty of chlorine to keep your pool sanitized.

(Body) About Us

A native to Phoenix, Daniel Harrow founded Tidewell Pools in 2000. Our company was built from the ground up by way of hard work, word of mouth, and determination. Our company will always remain firmly grounded, and continue to develop systems that put our customers first!

Our philosophy is to treat every pool as if it were our own, run an efficient and organized business, and care for our employees.

Tidewell Pools is a yearly, proud contributor to the Saguaro Youth Clinic Swim Smart Day. Please educate and watch all children around water... every accident can be avoided.

(Back) Contact Us

Office: 555-347-9180 | Fax: 555-347-9186 | Email: service@tidewellpools.example
tidewellpools.example

Office / Warehouse Location
41572 West 8th Street, Suite 4
Phoenix, Arizona 85999
(NW of 8th Street & Mesquite Ridge Road)

AZ ROC: 731150, 731151, 731152, 604378

Target Market(s)

We target a market of pool owners, which typically have more disposable income.

30 - 75 years old.

Our clients range from first-time home buyers, self-employed, business professionals, doctors, landlords, thousandaires, millionaires.

Industry/Entity Type

Pool Service

Font styles to use
Serif

Colors
0355a3
cfdfed
ffffff
3176b5
eaf1f7

Requirements
Must have
• Must use provided images. We've included a few pool pictures, and will let you decide which ones to incorporate throughout the brochure.

Logos Used:
Tidewell Pools
Hydrovel
FMC
Corra's Picks
VRE
MQW
Saguaro Youth Clinic
Google+
Facebook

Image pic of some of our trucks.

Nice to have
• Equipment images worked in.
Should not have
• Cartoonish fonts or design. No "Love" hearts!!

```html
<!DOCTYPE html>
<html lang="en">
<head>
<meta charset="utf-8">
<title>Tidewell Pools Brochure</title>
<link rel="stylesheet" href="https://fonts.googleapis.com/css2?family=Oswald:wght@400;500&family=PT+Sans:wght@400;700&display=swap">
<style>
  :root {
    --page: #ececec;
    --sheet: #eaf1f7;
    --sheet-tint: #cfdfed;
    --blue: #0355a3;
    --blue-mid: #3176b5;
    --text: #1f2f47;
    --text-soft: #3d4f68;
    --cream: #ffffff;
    --frame: #9fb5cc;
  }
  * { margin: 0; padding: 0; box-sizing: border-box; }
  html, body { width: 1200px; height: 857px; overflow: hidden; }
  body { background: var(--page); font-family: "PT Sans", sans-serif; position: relative; }

  .brochure { position: absolute; left: 43px; top: 35px; width: 1115px; height: 788px; background: var(--sheet); overflow: hidden; }
  .brochure > * { position: absolute; }
  .footer-band { left: 0; bottom: 0; width: 100%; height: 20px; background: var(--blue); }

  .label { background: var(--blue); color: #fff; font-family: "Oswald", sans-serif; font-weight: 400; font-size: 16px; letter-spacing: .5px; line-height: 25px; padding-left: 9px; height: 25px; }
  .label-about { left: 28px; top: 30px; width: 147px; }
  .label-contact { left: 401px; top: 591px; width: 147px; font-size: 15px; }

  .about-text { left: 29px; top: 65px; width: 314px; color: var(--text); font-size: 14px; line-height: 17.8px; text-align: justify; }

  .photo { border: 2px solid var(--frame); }
  .photo-a { left: 29px; top: 327px; width: 145px; height: 145px; background: linear-gradient(180deg, #a9b7c4 0%, #7d8f86 45%, #3f6b6a 65%, #a08f76 100%); }
  .photo-b { left: 196px; top: 327px; width: 146px; height: 145px; background: linear-gradient(160deg, #5d7a45 0%, #a48a6e 40%, #3b8fa8 70%, #cdbfa8 100%); }
  .photo-c { left: 29px; top: 503px; width: 145px; height: 145px; background: linear-gradient(180deg, #cbd7de 0%, #5f7558 40%, #3d6f8a 70%, #b8ab96 100%); }
  .photo-d { left: 196px; top: 503px; width: 146px; height: 145px; background: linear-gradient(180deg, #6f7a5a 0%, #d6c6a6 35%, #3ea3b6 65%, #c7b79b 100%); }
  .photo-e { left: 402px; top: 248px; width: 146px; height: 143px; background: linear-gradient(170deg, #8e7458 0%, #3d6f74 45%, #2b8fa0 75%, #c9b79a 100%); }
  .photo-f { left: 402px; top: 420px; width: 146px; height: 144px; background: linear-gradient(180deg, #3f7480 0%, #8a6f58 40%, #6f5a49 70%, #1f5f7e 100%); }
  .photo-hero { left: 575px; top: 248px; width: 353px; height: 316px; background: linear-gradient(180deg, #7c8fb2 0%, #5c7a5a 30%, #8a7a68 50%, #3b7f8f 72%, #2c6f86 100%); }
  .hero-veil { left: 577px; top: 250px; width: 166px; height: 312px; background: rgba(3, 85, 163, .35); }

  .hero-headline { left: 587px; top: 452px; color: #fff; font-family: "Oswald", sans-serif; font-weight: 400; font-size: 32px; line-height: 38px; letter-spacing: -.5px; }
  .hero-sub { left: 588px; top: 534px; color: #fff; font-family: "Oswald", sans-serif; font-size: 12px; letter-spacing: 1.2px; }

  .service-tag { background: var(--blue); color: var(--cream); font-family: "Oswald", sans-serif; font-size: 31px; line-height: 53px; padding-left: 14px; height: 53px; }
  .tag-service { left: 932px; top: 317px; width: 122px; }
  .tag-repair { left: 932px; top: 375px; width: 112px; }
  .tag-renovation { left: 932px; top: 433px; width: 170px; }

  .intro-lines { left: 740px; top: 22px; width: 364px; text-align: center; color: var(--blue); font-family: "Oswald", sans-serif; font-weight: 500; font-size: 12px; line-height: 22px; letter-spacing: .6px; }

  .info-col { top: 100px; width: 176px; color: var(--text); }
  .info-why { left: 748px; }
  .info-method { left: 934px; }
  .info-title { font-family: "Oswald", sans-serif; font-weight: 500; font-size: 13px; color: var(--blue); letter-spacing: .5px; border-bottom: 1px solid var(--blue-mid); padding-bottom: 2px; margin-bottom: 5px; }
  .info-list { list-style: none; font-size: 10px; line-height: 13.5px; }
  .info-list li { padding-left: 9px; position: relative; margin-bottom: 2px; }
  .info-list li::before { content: ""; position: absolute; left: 0; top: 5px; width: 4px; height: 4px; background: var(--blue-mid); }

  .brand { display: flex; flex-direction: column; color: var(--blue); font-family: "PT Sans", sans-serif; font-weight: 700; }
  .brand-row { display: flex; align-items: center; gap: 10px; }
  .brand-dot { width: 34px; height: 34px; border-radius: 50%; background: var(--blue); flex: none; }
  .brand-name { font-size: 36px; line-height: 1; }
  .brand-motto { font-size: 13px; align-self: flex-end; margin-top: 2px; }
  .brand-top { left: 404px; top: 110px; }
  .brand-left { left: 66px; top: 690px; }
  .brand-left .brand-name { font-size: 30px; }
  .brand-left .brand-dot { width: 28px; height: 28px; }
  .brand-right { left: 772px; top: 668px; }

  .partner { background: var(--sheet-tint); }
  .partner-a { left: 570px; top: 594px; width: 80px; height: 22px; transform: skewX(-12deg); }
  .partner-b { left: 663px; top: 593px; width: 72px; height: 28px; border-radius: 2px; }
  .partner-c { left: 617px; top: 637px; width: 70px; height: 24px; border-radius: 12px; }

  .contact-list { left: 402px; top: 661px; list-style: none; color: var(--text); font-size: 9.5px; }
  .contact-list li { display: flex; align-items: center; gap: 6px; height: 19.6px; }
  .contact-list svg { width: 9px; height: 9px; flex: none; }

  .address { left: 562px; top: 681px; width: 180px; text-align: center; color: var(--text); font-size: 8.6px; font-weight: 700; line-height: 13px; }
</style>
</head>
<body>
<main class="brochure">
  <div class="label label-about">ABOUT US</div>
  <div class="about-text">
    <p>A native to Phoenix, Daniel Harrow founded Tidewell Pools in 2000. Our company was built from the ground up by way of hard work, word of mouth, and determination. Our company will always remain firmly grounded, and continue to develop systems that put our customers first!</p>
    <p>Our philosophy is to treat every pool as if it were our own, run an efficient and organized business, and care for our employees.</p>
    <p>Tidewell Pools is a yearly, proud contributor to the Saguaro Youth Clinic Swim Smart Day. Please educate and watch all children around water... every accident can be avoided.</p>
  </div>

  <div class="photo photo-a" role="img" aria-label="Natural rock pool with spa under a cloudy desert sky"></div>
  <div class="photo photo-b" role="img" aria-label="Pool with rock waterfall and flowering planter"></div>
  <div class="photo photo-c" role="img" aria-label="Pool with palm fronds and mountain view"></div>
  <div class="photo photo-d" role="img" aria-label="Backyard pool with potted agave"></div>

  <div class="brand brand-left">
    <div class="brand-row"><span class="brand-dot"></span><span class="brand-name">Tidewell Pools</span></div>
    <span class="brand-motto">Every Ripple Counts</span>
  </div>

  <div class="brand brand-top">
    <div class="brand-row"><span class="brand-dot"></span><span class="brand-name">Tidewell Pools</span></div>
    <span class="brand-motto">Every Ripple Counts</span>
  </div>

  <div class="intro-lines">
    PROVIDING SWIMMING POOL SERVICE,<br>REPAIR, AND CUSTOM RENOVATIONS<br>THROUGHOUT THE PHOENIX, ARIZONA METROPOLITAN AREA
  </div>

  <section class="info-col info-why">
    <h2 class="info-title">WHY CHOOSE US?</h2>
    <ul class="info-list">
      <li>Licensed, bonded and fully insured</li>
      <li>All technicians are employees, not sub-contractors</li>
      <li>Flat-fee service rates, no contracts</li>
      <li>Detailed service slips after every visit</li>
      <li>10% client discount on all repairs</li>
    </ul>
  </section>

  <section class="info-col info-method">
    <h2 class="info-title">OUR METHODOLOGY</h2>
    <ul class="info-list">
      <li>Good, clean water</li>
      <li>Efficient water flow</li>
      <li>Proper filtration</li>
      <li>Functioning cleaning system</li>
      <li>A dependable, professional technician</li>
    </ul>
  </section>

  <div class="photo photo-e" role="img" aria-label="Stone spillway into a pool"></div>
  <div class="photo photo-f" role="img" aria-label="Stacked stone water feature"></div>
  <div class="photo photo-hero" role="img" aria-label="Rock waterfall pool with palms and mist"></div>
  <div class="hero-veil"></div>
  <div class="hero-headline">ECONOMICAL<br>&amp; PROFESSIONAL</div>
  <div class="hero-sub">MAKING YOUR POOL SPECIAL</div>

  <div class="service-tag tag-service">SERVICE</div>
  <div class="service-tag tag-repair">REPAIR</div>
  <div class="service-tag tag-renovation">RENOVATION</div>

  <div class="label label-contact">CONTACT US &nbsp;- 24/7</div>
  <div class="partner partner-a" role="img" aria-label="Utility partner badge"></div>
  <div class="partner partner-b" role="img" aria-label="Clinic partner badge"></div>
  <div class="partner partner-c" role="img" aria-label="Utility partner badge"></div>

  <ul class="contact-list">
    <li><svg viewBox="0 0 10 10"><path d="M2 1 L4 1 L4.6 3 L3.4 3.8 Q4.3 5.8 6.2 6.6 L7 5.4 L9 6 L9 8 Q5 9.5 1.5 5 Q0.8 2.5 2 1Z" fill="#3176b5"/></svg>555-347-9180</li>
    <li><svg viewBox="0 0 10 10"><path d="M5 1 L9.5 5 L8 5 L8 9 L2 9 L2 5 L0.5 5Z" fill="#3176b5"/></svg>www.tidewellpools.example</li>
    <li><svg viewBox="0 0 10 10"><rect width="10" height="10" fill="#3176b5"/></svg>tidewellpools</li>
    <li><svg viewBox="0 0 10 10"><rect width="10" height="10" fill="#0355a3"/></svg>+Tidewellpools</li>
  </ul>

  <div class="address">
    Office / Warehouse Location<br>
    41572 West 8th Street, Suite 4<br>
    Phoenix, Arizona 85999<br>
    (NW of 8th Street &amp; Mesquite Ridge Road)
  </div>

  <div class="brand brand-right">
    <div class="brand-row"><span class="brand-dot"></span><span class="brand-name">Tidewell Pools</span></div>
    <span class="brand-motto">Every Ripple Counts</span>
  </div>

  <div class="footer-band"></div>
</main>
</body>
</html>
```